Report template for evaluation reports to be used by non designers

We are looking for a report template that meets all the requirements listed in the attached documents. letter head, logo etc have been enclosed. Its important that the colour integrity is kept, but beyond that options are welcome.
Its important that the document is extremely easy to use and that is able to be adapted to include eatables, figures, pictures, text boxes etc and keep the integrity of the template

Target Market(s)

Governments, Civil society organisations and research institutions

Font styles to use
Sans Serif

Colors
6b449b
876aae
c0c0c0
000000

Requirements
Must have
• Clean, professional, not concluded, modern, must be easy to use
Should not have
• too busy, hard to use

```html
<!DOCTYPE html>
<html lang="en">
<head>
<meta charset="utf-8">
<title>Meridian Policy Lab – Report Covers</title>
<link rel="stylesheet" href="https://fonts.googleapis.com/css2?family=Open+Sans:wght@400;600;700&display=swap">
<style>
  :root{
    --purple:#6b449b;
    --purple-soft:#876aae;
    --silver:#c0c0c0;
    --ink:#000000;
    --paper:#f4f4f6;
    --backdrop:#a7a7aa;
  }
  *{box-sizing:border-box;margin:0;padding:0}
  html,body{width:1200px;height:925px;overflow:hidden}
  body{background:var(--backdrop);font-family:"Open Sans",Arial,sans-serif;color:var(--ink);position:relative}
  .spread{position:absolute;left:80px;top:95px;width:1040px;height:735px;display:flex;box-shadow:0 18px 40px rgba(0,0,0,.25)}
  .page{position:relative;width:520px;height:735px;background:var(--paper);overflow:hidden}
  .page--back{background:#ececef;border-right:1px solid #d6d6da}
  .page-art{position:absolute;inset:0;width:100%;height:100%}
  .brand{position:absolute;left:42px;top:34px;font-size:24px;font-weight:600;color:#2a2a2a;letter-spacing:.5px}
  .report-title{position:absolute;left:48px;top:376px;width:420px;font-size:23px;line-height:1.3;font-weight:700;color:var(--purple)}
  .meta{position:absolute;left:58px;display:grid;grid-template-columns:82px auto;row-gap:8px;font-size:14px}
  .meta dt{color:var(--purple);font-weight:700}
  .meta dd{color:#222}
  .meta--front{top:470px}
  .meta--back{top:548px}
  .thanks{position:absolute;left:60px;top:300px;font-size:44px;font-weight:700;color:var(--purple)}
  .url-pill{position:absolute;height:22px;padding:0 14px;border:2px solid var(--purple);border-radius:11px;background:var(--paper);font-size:9.5px;font-weight:700;line-height:18px;color:#222}
  .page--back .url-pill{background:#ececef}
  .url-pill--front{left:255px;top:640px}
  .url-pill--back{left:180px;top:652px}
</style>
</head>
<body>
<main class="spread">
  <section class="page page--back" aria-label="Back cover">
    <svg class="page-art" viewBox="0 0 520 735" aria-hidden="true">
      <path d="M0,685 Q260,655 520,628" fill="none" stroke="var(--purple)" stroke-width="2"/>
    </svg>
    <h2 class="thanks">Thank You!</h2>
    <dl class="meta meta--back">
      <dt>Email:</dt><dd>info@meridianpolicylab.org</dd>
      <dt>ISBN:</dt><dd>CHF-467.113.214</dd>
    </dl>
    <span class="url-pill url-pill--back">www.meridianpolicylab.org</span>
  </section>

  <section class="page page--front" aria-label="Front cover">
    <svg class="page-art" viewBox="0 0 520 735">
      <defs>
        <linearGradient id="photoTone" x1="0" y1="0" x2="1" y2="1">
          <stop offset="0" stop-color="#cfd6df"/>
          <stop offset=".5" stop-color="#e6e9ee"/>
          <stop offset="1" stop-color="#8a8f99"/>
        </linearGradient>
      </defs>
      <path role="img" aria-label="Photo of a team meeting around a table reviewing documents"
            d="M40,100 Q280,96 520,62 L520,300 Q280,318 40,350 Z" fill="url(#photoTone)"/>
      <path d="M0,108 Q280,100 520,58" fill="none" stroke="var(--purple)" stroke-width="3"/>
      <path d="M40,352 Q280,320 520,302" fill="none" stroke="var(--purple)" stroke-width="3"/>
      <path d="M0,690 Q260,668 520,612" fill="none" stroke="var(--purple)" stroke-width="2"/>
    </svg>
    <div class="brand">Meridian Policy Lab</div>
    <h1 class="report-title">Pre-Study for an Impact Evaluation of the ABC programme</h1>
    <dl class="meta meta--front">
      <dt>Client:</dt><dd>ABC Company</dd>
      <dt>Date:</dt><dd>September 22, 2018</dd>
    </dl>
    <span class="url-pill url-pill--front">www.meridianpolicylab.org</span>
  </section>
</main>
</body>
</html>
```